Audio/ Video Packaging Design for a Technology company.

We need a packaging design for a bag that is 7" wide and 10" high. The design will be for a new line of audio/video products. We would like to see designs that represent a superior quality product that provides a pure connection. We want the equivalent of a nice retail bag that you would find in a store like Tallow Mart. It should be a maximum of three colors. We really want something sharp, professional and eye catching, not whimsical or cartoonish. I've included a couple of examples below. I don't really like the designs of the bags, but I want you to see examples of what I'm looking for.

The company logo, which is uploaded, should be on the design. The words "audio and video products" should be either underneath the logo or to the side. Also, somewhere on the bag, we would like the words "For a Pure Connection"

The winner of this contest will likely get the opportunity for additional work as we have more products ready to launch.

Target Market(s)

resellers, consumers - men 25-60

Industry/Entity Type

It Company

Requirements
Must have
• It should be a maximum of three colors. We really want something sharp, professional and eye catching, not whimsical or cartoonish
Nice to have
• Eye-catching design. Utilize the entire bag but don't make it too busy.
Should not have
• Whimsical, cartoonish

```html
<!DOCTYPE html>
<html lang="en">
<head>
<meta charset="utf-8">
<title>Veridan Package Design</title>
<link href="https://fonts.googleapis.com/css2?family=Montserrat:wght@400;500;600&display=swap" rel="stylesheet">
<style>
  :root {
    --stage: #8d8d8d;
    --stage-light: #b4b4b4;
    --bag-grey: #3c3d40;
    --bag-white: #ffffff;
    --sky-blue: #4fb3ea;
    --deep-blue: #2f74c8;
    --ink: #2b2f36;
    --muted: #8a8b8e;
  }
  * { box-sizing: border-box; margin: 0; padding: 0; }
  html, body { width: 1200px; height: 960px; overflow: hidden; }
  body {
    font-family: "Montserrat", sans-serif;
    background: linear-gradient(160deg, var(--stage) 0%, var(--stage-light) 100%);
    position: relative;
  }
  .board-title {
    position: absolute; right: 56px; top: 52px; text-align: right;
  }
  .board-title .brand {
    display: flex; align-items: center; justify-content: flex-end; gap: 14px;
    font-size: 50px; font-weight: 500; color: var(--ink); letter-spacing: 2px; line-height: 1;
  }
  .board-title .brand-square { width: 34px; height: 34px; background: var(--sky-blue); }
  .board-title .subtitle {
    margin-top: 14px; font-size: 21px; font-weight: 500; color: #f2f2f2; letter-spacing: 1px;
  }
  .bag { position: absolute; top: 206px; width: 481px; height: 712px; }
  .bag-front { left: 61px; }
  .bag-back { left: 654px; }
  .bag svg { display: block; width: 100%; height: 100%; }
  .brand-name { font-family: "Montserrat", sans-serif; font-weight: 500; fill: #fff; }
  .tagline { font-family: "Montserrat", sans-serif; font-weight: 500; fill: #fff; font-size: 22px; }
  .product-line { font-family: "Montserrat", sans-serif; font-weight: 500; font-size: 16px; letter-spacing: 2.6px; }
  .origin { font-family: "Montserrat", sans-serif; font-size: 8px; letter-spacing: 1px; fill: var(--muted); }
</style>
</head>
<body>

<header class="board-title">
  <div class="brand"><span class="brand-square"></span>Veridan</div>
  <div class="subtitle">PACKAGE DESIGN</div>
</header>

<!-- Front face -->
<div class="bag bag-front">
  <svg viewBox="0 0 481 712" xmlns="http://www.w3.org/2000/svg">
    <defs>
      <clipPath id="front-shape"><rect width="481" height="712" rx="32"/></clipPath>
      <linearGradient id="front-window" x1="0" y1="0" x2="1" y2="1">
        <stop offset="0" stop-color="#d9d9d9"/>
        <stop offset="0.5" stop-color="#9a9a9a"/>
        <stop offset="1" stop-color="#4a4a4a"/>
      </linearGradient>
    </defs>
    <g clip-path="url(#front-shape)">
      <rect class="bag-body" width="481" height="712" fill="var(--bag-white)"/>
      <line x1="10" y1="94" x2="471" y2="94" stroke="#dcdcdc" stroke-dasharray="4 4"/>
      <rect x="43" y="104" width="394" height="440" rx="18" fill="url(#front-window)" role="img" aria-label="Coiled black power cable with connector seen through the clear window"/>
      <polygon class="accent-band" points="0,272 282,512 481,200 481,218 284,530 0,290" fill="var(--sky-blue)"/>
      <polygon class="panel" points="0,298 285,546 481,228 481,712 0,712" fill="var(--bag-grey)"/>
      <rect x="155" y="552" width="26" height="26" fill="var(--sky-blue)"/>
      <text class="brand-name" x="193" y="580" font-size="46">Veridan</text>
      <text class="product-line" x="155" y="628" fill="var(--sky-blue)">audio and video products</text>
      <text class="tagline" x="154" y="672">“For a Pure Connection”</text>
      <text class="origin" transform="translate(25,650) rotate(-90)">MADE IN CHINA</text>
    </g>
  </svg>
</div>

<!-- Back face -->
<div class="bag bag-back">
  <svg viewBox="0 0 481 712" xmlns="http://www.w3.org/2000/svg">
    <defs>
      <clipPath id="back-shape"><rect width="481" height="712" rx="32"/></clipPath>
      <linearGradient id="back-window" x1="0" y1="0" x2="1" y2="1">
        <stop offset="0" stop-color="#e0e0e0"/>
        <stop offset="0.5" stop-color="#8f8f8f"/>
        <stop offset="1" stop-color="#3e3e3e"/>
      </linearGradient>
    </defs>
    <g clip-path="url(#back-shape)">
      <rect width="481" height="712" fill="var(--bag-white)"/>
      <line x1="10" y1="94" x2="471" y2="94" stroke="#dcdcdc" stroke-dasharray="4 4"/>
      <rect x="54" y="112" width="372" height="460" rx="18" fill="url(#back-window)" role="img" aria-label="Coiled black power cable with connector seen through the clear window"/>
      <rect x="112" y="140" width="26" height="26" fill="var(--deep-blue)"/>
      <text x="150" y="168" font-size="42" font-weight="500" fill="var(--ink)" font-family="Montserrat, sans-serif">Veridan</text>
      <rect x="94" y="184" width="304" height="28" rx="5" fill="var(--bag-grey)"/>
      <text class="product-line" x="246" y="204" fill="var(--sky-blue)" text-anchor="middle" font-size="15">audio and video products</text>
      <polygon points="0,306 302,560 481,236 481,256 304,580 0,326" fill="var(--deep-blue)"/>
      <polygon points="0,334 306,590 481,266 481,712 0,712" fill="var(--bag-grey)"/>
      <text class="origin" transform="translate(43,534) rotate(-90)">MADE IN CHINA</text>
      <rect x="28" y="543" width="30" height="103" fill="none" stroke="var(--sky-blue)" stroke-width="2"/>
      <rect x="28" y="543" width="30" height="103" fill="var(--sky-blue)"/>
      <text transform="translate(52,642) rotate(-90)" font-family="Montserrat, sans-serif" font-weight="500" font-size="24" fill="var(--bag-grey)">POWER</text>
      <text transform="translate(81,642) rotate(-90)" font-family="Montserrat, sans-serif" font-weight="500" font-size="20" fill="var(--sky-blue)">110V ~300V</text>
      <text x="90" y="646" font-family="Montserrat, sans-serif" font-weight="600" font-size="74" fill="var(--sky-blue)">CABLE</text>
      <line x1="90" y1="653" x2="330" y2="653" stroke="var(--sky-blue)" stroke-width="2"/>
      <text class="tagline" x="212" y="676" text-anchor="middle" font-size="20">“For a Pure Connection”</text>
    </g>
  </svg>
</div>

</body>
</html>
```